Velmarotix - world unique technology for better life - please let them know who am i at first sight

We need a new business card for company which is a provider of unique crystal based technology suitable for all living being. For more information and final design you can use our brochure (our colours are black and blue from brochure).
We use Verdana font

Industry/Entity Type

Business

Contact Information for Business Card

regular dimension

Font styles to use
Other font styles liked:
• Verdana

Requirements
Must have
• Logo
• name
• function/position
• phone
• mobile
• e-mail
• adress
Nice to have
• inovative design (technology directed)

```html
<!DOCTYPE html>
<html lang="en">
<head>
<meta charset="utf-8">
<title>Velmarotix – Business Card</title>
<link rel="stylesheet" href="https://fonts.googleapis.com/css2?family=Exo+2:wght@400;500;700&display=swap">
<style>
  :root {
    --brand-blue: #29a9e1;
    --brand-blue-dark: #1d93c9;
    --band-grey: #a3a7ab;
    --ink: #1f2326;
    --card-white: #fbfcfd;
    --backdrop: #e9ecef;
    --on-blue: #ffffff;
  }
  * { box-sizing: border-box; margin: 0; padding: 0; }
  html, body {
    width: 1200px; height: 901px; overflow: hidden;
    background: var(--backdrop);
    font-family: "Exo 2", Verdana, sans-serif;
  }
  .business-card {
    position: absolute; left: 150px; top: 193px;
    width: 900px; height: 515px;
    border-radius: 48px; overflow: hidden;
    background: var(--card-white);
    box-shadow: 0 10px 30px rgba(0,0,0,0.15);
  }
  .card-waves { position: absolute; inset: 0; }
  .brand {
    position: absolute; left: 60px; top: 52px;
    display: flex; align-items: center; gap: 18px;
  }
  .brand-dot {
    width: 70px; height: 70px; border-radius: 50%;
    background: var(--brand-blue);
  }
  .brand-name {
    font-size: 46px; font-weight: 500; letter-spacing: 2px;
    color: var(--brand-blue); text-transform: uppercase;
  }
  .holder { position: absolute; left: 60px; top: 180px; }
  .holder-name {
    font-size: 31px; font-weight: 700; letter-spacing: 1.5px;
    color: var(--ink); text-transform: uppercase; line-height: 1.1;
  }
  .holder-role {
    font-size: 21px; font-weight: 500; letter-spacing: 0.5px;
    color: var(--brand-blue); margin-top: 2px;
  }
  .contact {
    position: absolute; right: 60px; top: 290px;
    color: var(--on-blue); text-align: right;
    font-size: 17px; font-weight: 500; letter-spacing: 0.8px;
  }
  .contact-address { line-height: 24px; margin-bottom: 18px; }
  .contact-list { list-style: none; }
  .contact-item {
    display: flex; justify-content: flex-end; align-items: center;
    gap: 10px; height: 27px;
  }
  .contact-icon { width: 17px; height: 17px; flex: none; }
</style>
</head>
<body>
  <article class="business-card">
    <svg class="card-waves" viewBox="0 0 900 515" width="900" height="515" aria-hidden="true">
      <path d="M0,318 C220,368 430,332 620,292 S840,242 900,238 L900,515 L0,515 Z" fill="var(--brand-blue)"/>
      <path d="M0,318 C220,368 430,332 620,292 S840,242 900,238" fill="none" stroke="var(--band-grey)" stroke-width="13" transform="translate(0,-20)"/>
      <path d="M0,318 C220,368 430,332 620,292 S840,242 900,238" fill="none" stroke="var(--brand-blue)" stroke-width="4" transform="translate(0,-40)"/>
    </svg>

    <div class="brand">
      <span class="brand-dot"></span>
      <span class="brand-name">Velmarotix</span>
    </div>

    <div class="holder">
      <h1 class="holder-name">Daniel Morrow</h1>
      <p class="holder-role">Managing Director</p>
    </div>

    <address class="contact" style="font-style:normal">
      <p class="contact-address">27 Orwen Plaza, Level 9<br>Halden Street KRV</p>
      <ul class="contact-list">
        <li class="contact-item">014 628 3907
          <svg class="contact-icon" viewBox="0 0 24 24" aria-label="Phone"><path d="M6.6 10.8a15.2 15.2 0 0 0 6.6 6.6l2.2-2.2a1 1 0 0 1 1-.25 11.4 11.4 0 0 0 3.6.57 1 1 0 0 1 1 1V20a1 1 0 0 1-1 1A17 17 0 0 1 3 4a1 1 0 0 1 1-1h3.5a1 1 0 0 1 1 1c0 1.25.2 2.45.57 3.57a1 1 0 0 1-.25 1z" fill="currentColor"/></svg>
        </li>
        <li class="contact-item">014 628 3908
          <svg class="contact-icon" viewBox="0 0 24 24" aria-label="Mobile"><rect x="6" y="2" width="12" height="20" rx="2" fill="none" stroke="currentColor" stroke-width="2"/><circle cx="12" cy="18" r="1.2" fill="currentColor"/></svg>
        </li>
        <li class="contact-item">014 628 3909
          <svg class="contact-icon" viewBox="0 0 24 24" aria-label="Fax"><rect x="7" y="3" width="10" height="6" fill="none" stroke="currentColor" stroke-width="2"/><rect x="3" y="9" width="18" height="12" rx="1.5" fill="currentColor"/></svg>
        </li>
        <li class="contact-item">hello@velmarotix.com
          <svg class="contact-icon" viewBox="0 0 24 24" aria-label="Email"><rect x="2" y="5" width="20" height="14" rx="1.5" fill="currentColor"/><path d="M3 6l9 7 9-7" fill="none" stroke="var(--brand-blue)" stroke-width="1.8"/></svg>
        </li>
        <li class="contact-item">www.velmarotix.com
          <svg class="contact-icon" viewBox="0 0 24 24" aria-label="Website"><circle cx="12" cy="12" r="9.5" fill="none" stroke="currentColor" stroke-width="2"/><path d="M2.5 12h19M12 2.5c3 3 3 16 0 19M12 2.5c-3 3-3 16 0 19" fill="none" stroke="currentColor" stroke-width="1.6"/></svg>
        </li>
      </ul>
    </address>
  </article>
</body>
</html>
```